redesign of my existing custom website into Wordpress based website

I need someone to redesign my current website into something more classy, simplistic, modern and on trend. I would like it set up on Wordpress in a way thats easy for me to make my own additions to blogs/price changes and promotion banners. I will also need a page that is password protected so members can login and have access to all my training videos and resources.
website is www.tidewellmamas.com.au

Target Market(s)

new mums

Industry/Entity Type

Fitness

Coding

Coded - Design and coding required

Number of Pages Required

5+ page

Colors
33a6d7

Requirements
Must have
• chic, modern, stylish and simplistic.
• a call to action above the page fold
• mobile friendly conversion
• a pop up message as soon as someone enters my sight offering my free report
• a members page that is password protected containing 3 youtube videos and 6 pdf attachments as resources
• a home page
• a contact us page
• an about us page
• a blog page
• a store page
Nice to have
• some examples of my peers websites that I like:
• www.norapellwick.com
• https://www.9qlr.com
• https://41bytedgarth.com
Should not have
• anything gimmicky

```html
<!DOCTYPE html>
<html lang="en">
<head>
<meta charset="utf-8">
<title>Harbourleaf Mums – Home</title>
<link href="https://fonts.googleapis.com/css2?family=Open+Sans:wght@300;400;600;700;800&display=swap" rel="stylesheet">
<style>
:root{
  --brand:#33a6d7;
  --brand-deep:#2383b3;
  --brand-panel:#2a8fc0;
  --ink:#222;
  --muted:#777;
  --dark:#1b1d20;
  --white:#fff;
  --line:#e2e2e2;
  --scrim:rgba(0,0,0,.72);
}
*{margin:0;padding:0;box-sizing:border-box}
html,body{width:1200px;height:4225px;overflow:hidden}
body{font-family:"Open Sans",Arial,sans-serif;color:var(--ink);background:var(--white);position:relative}
section,header,footer{position:absolute;left:0;width:1200px}

/* header / hero */
.hero{top:0;height:797px}
.hero-photo{position:absolute;inset:0;background:linear-gradient(120deg,#6b6560 0%,#b9aea5 35%,#8c8178 65%,#3f3a36 100%)}
.brand{position:absolute;left:186px;top:22px;display:flex;flex-direction:column;align-items:center;gap:6px;width:110px;color:var(--white);font-weight:700;font-size:12px;text-align:center}
.brand-dot{width:84px;height:84px;border-radius:50%;background:var(--white)}
.nav{position:absolute;top:58px;left:515px;display:flex}
.nav a{color:var(--white);text-decoration:none;font-size:15px;font-weight:600;margin-right:44px}
.nav a.active{border-bottom:2px solid var(--brand);padding-bottom:4px}
.slider-dots{position:absolute;top:702px;left:0;width:1200px;display:flex;justify-content:center;gap:14px}
.slider-dots i{width:10px;height:10px;border-radius:50%;background:var(--white);opacity:.6}

/* offer panels */
.offer{top:797px;height:550px}
.offer-left{position:absolute;left:0;top:0;width:600px;height:550px;background:linear-gradient(160deg,var(--brand-panel),var(--brand-deep))}
.offer-right{position:absolute;left:600px;top:0;width:600px;height:550px;background:var(--white)}
.offer h2{font-size:40px;line-height:52px;font-weight:700}
.offer-left h2{position:absolute;left:127px;top:60px;color:var(--white)}
.price-from{position:absolute;left:127px;top:262px;color:var(--white);font-size:22px;font-weight:600}
.price{position:absolute;left:127px;top:300px;color:var(--white);font-size:46px;font-weight:300}
.price b{font-weight:700}
.btn{position:absolute;display:flex;align-items:center;justify-content:center;font-size:15px;font-weight:700;text-transform:uppercase;letter-spacing:.5px}
.btn-ghost{border:2px solid var(--white);color:var(--white);background:rgba(255,255,255,.12)}
.btn-solid{background:var(--brand);color:var(--white)}
.offer-right h2{position:absolute;left:22px;top:60px;color:var(--ink);font-size:38px;line-height:50px}
.offer-right p{position:absolute;left:22px;top:172px;width:460px;font-size:15px;color:var(--muted);line-height:22px}
.field{position:absolute;left:22px;width:460px;height:52px;border-bottom:1px solid var(--line);font-size:14px;color:#aaa;padding:16px 12px}

/* testimonials */
.testimonials{top:1347px;height:757px;background:var(--white);text-align:center}
.avatar{position:absolute;top:199px;width:170px;height:170px;border-radius:50%;border:4px solid var(--white);box-shadow:0 0 0 2px var(--line);background:radial-gradient(circle at 50% 45%,#c9a98e,#6a8fa6)}
.avatar-label{position:absolute;top:374px;width:170px;font-size:12px;color:var(--muted)}
.t-name{position:absolute;top:410px;width:1200px;font-size:34px;font-weight:700;color:var(--brand)}
.t-role{position:absolute;top:455px;width:1200px;font-size:16px;color:var(--ink)}
.t-sub{position:absolute;top:484px;width:1200px;font-size:12px;color:var(--muted)}
.t-quote{position:absolute;top:535px;left:120px;width:960px;font-size:14px;line-height:26px;color:var(--muted)}
.t-dots{position:absolute;top:672px;width:1200px;display:flex;justify-content:center;gap:12px}
.t-dots i{width:10px;height:10px;border-radius:50%;background:#ccc}
.t-dots i.on{background:var(--brand)}

/* program */
.program{top:2104px;height:417px;background:var(--dark);text-align:center}
.program h3{position:absolute;width:1200px;font-size:30px;font-weight:700;color:var(--brand)}
.program p{position:absolute;width:1200px;color:#cfd3d6}
.rule{position:absolute;left:492px;top:218px;width:216px;height:2px;background:#9aa1a6}

/* payment band */
.payment{top:2521px;height:133px;background:var(--brand);text-align:center;color:var(--white)}
.payment h3{position:absolute;top:26px;width:1200px;font-size:30px;font-weight:700}
.payment p{position:absolute;top:76px;width:1200px;font-size:22px}
.arrow{position:absolute;top:50px}

/* features */
.features{top:2654px;height:825px;background:var(--white)}
.features h2{position:absolute;top:66px;width:1200px;text-align:center;font-size:32px;font-weight:700}
.feature{position:absolute;width:440px}
.feature svg{position:absolute;left:0;top:0}
.feature h4{position:absolute;left:72px;top:2px;font-size:19px;font-weight:700;color:var(--brand);line-height:26px}
.feature p{position:absolute;left:0;top:80px;width:440px;font-size:13px;line-height:22px;color:var(--muted)}
.feature .btn{left:0;top:200px;width:108px;height:34px;font-size:12px;text-transform:none}

/* call to action */
.cta{top:3479px;height:380px;background:linear-gradient(120deg,#2a8fc0,#1e6f98 60%,#2a8fc0)}
.cta h2{position:absolute;top:155px;width:1200px;text-align:center;color:var(--white);font-size:30px;font-weight:700;line-height:40px}

/* footer */
.site-footer{top:3859px;height:366px;background:var(--white)}
.footer-brand{position:absolute;left:150px;top:84px;width:112px;display:flex;flex-direction:column;align-items:center;gap:6px;font-weight:700;font-size:11px;line-height:14px;color:var(--brand);text-align:center}
.footer-brand .brand-dot{width:70px;height:70px;background:var(--brand)}
.f-col{position:absolute;top:60px}
.f-col h5{font-size:15px;font-weight:700;color:var(--brand);margin-bottom:14px}
.f-col p,.f-col li{font-size:12px;line-height:22px;color:var(--muted);list-style:none}
.copyright{position:absolute;top:322px;width:1200px;text-align:center;font-size:11px;color:#999}

/* scrim + popup */
.scrim{position:absolute;left:0;top:0;width:1200px;height:4225px;background:var(--scrim)}
.popup{position:absolute;left:304px;top:240px;width:597px;height:464px;overflow:hidden}
.popup-photo{position:absolute;inset:0;background:linear-gradient(90deg,#bdbdbd,#e6e6e6 45%,#cfcfcf)}
.popup-close{position:absolute;left:553px;top:14px;width:30px;height:30px;border-radius:50%;background:var(--white);border:2px solid #555}
.popup h2{position:absolute;top:100px;width:597px;text-align:center;font-size:40px;font-weight:800;color:var(--brand)}
.popup h3{position:absolute;top:148px;width:597px;text-align:center;font-size:30px;font-weight:400;color:#333}
.popup .email{position:absolute;left:34px;top:225px;width:524px;height:59px;background:var(--white);border-radius:3px;font-size:14px;color:#555;padding:20px 16px}
.popup .subscribe{left:34px;top:312px;width:524px;height:62px;font-size:22px;border-radius:3px}
</style>
</head>
<body>

<header class="hero">
  <div class="hero-photo" role="img" aria-label="Hero photo of a smiling new mum exercising at home"></div>
  <div class="brand"><span class="brand-dot"></span>Harbourleaf Mums</div>
  <nav class="nav">
    <a class="active">Home</a><a>About Us</a><a>Program</a><a>Blog</a><a>Shop</a><a>Contact Us</a>
  </nav>
  <div class="slider-dots"><i></i><i></i><i></i><i></i><i></i></div>
</header>

<section class="offer">
  <div class="offer-left" role="img" aria-label="Blue tinted photo of a mum training">
    <h2>Start seeing<br>amazing results<br>in just a few weeks!</h2>
    <div class="price-from">Starting from</div>
    <div class="price">only <b>$7.50/Week!</b></div>
    <div class="btn btn-ghost" style="left:127px;top:426px;width:231px;height:59px">Get Started</div>
  </div>
  <div class="offer-right">
    <h2>Get your FREE top 10<br>Baby Belly Blasting Tips</h2>
    <p>Get our secret tips to a flatter post-baby tummy that you can start using today, free.</p>
    <div class="field" style="top:250px">First Name</div>
    <div class="field" style="top:328px">Email Address</div>
    <div class="btn btn-solid" style="left:22px;top:426px;width:229px;height:59px">Get It Free Now !</div>
  </div>
</section>

<section class="testimonials">
  <div class="avatar" style="left:416px" role="img" aria-label="Before photo of a program member"></div>
  <div class="avatar" style="left:614px" role="img" aria-label="After photo of a program member"></div>
  <div class="avatar-label" style="left:416px">Before</div>
  <div class="avatar-label" style="left:614px">After</div>
  <div class="t-name">Marisa</div>
  <div class="t-role">Harbourleaf Mums Founder</div>
  <div class="t-sub">Mum of two and program graduate</div>
  <p class="t-quote">After my second baby I felt tired and unsure of where to start. This program gave me a clear plan I could follow at home, with short sessions that fit around naps and feeds. Within twelve weeks my strength came back, my core felt stable and I had more energy for my family than ever before.</p>
  <div class="t-dots"><i class="on"></i><i></i><i></i><i></i></div>
</section>

<section class="program">
  <h3 style="top:68px">What's included in the program?</h3>
  <p style="top:118px;font-size:17px">12 Week Home Workout Program · Equipment Pack · Recipe Guide · Online Support</p>
  <div class="rule"></div>
  <h3 style="top:250px">Our unique 3 stage, 12 week training program</h3>
  <p style="top:300px;font-size:12px">Specially built for mums, each stage gently rebuilds your core, then strength, then fitness so you progress safely at your own pace.</p>
  <p style="top:326px;font-size:12px">Every stage adds new workouts and simple meals, guiding you from early recovery to feeling strong and confident.</p>
</section>

<section class="payment">
  <svg class="arrow" style="left:90px" width="20" height="32" viewBox="0 0 20 32"><path d="M16 3 4 16l12 13" fill="none" stroke="#111" stroke-width="3"/></svg>
  <h3>One time only payment of $199 *including GST</h3>
  <p>That's only $16.60 per week!</p>
  <svg class="arrow" style="left:1092px" width="20" height="32" viewBox="0 0 20 32"><path d="M4 3l12 13L4 29" fill="none" stroke="#111" stroke-width="3"/></svg>
</section>

<section class="features">
  <h2>Why our program is different ?</h2>

  <div class="feature" style="left:150px;top:190px">
    <svg width="52" height="52" viewBox="0 0 52 52"><g fill="none" stroke="#111" stroke-width="3"><circle cx="34" cy="10" r="5"/><path d="M12 24l14-8 8 10-10 10M26 16l-4 26M34 26l10 4"/></g></svg>
    <h4>Specially Designed For Mums</h4>
    <p>Every workout is planned around the needs of a recovering body, with safe moves for the core and pelvic floor, short timings and clear guidance so you always know what to do next at home.</p>
    <div class="btn btn-solid">Read More</div>
  </div>

  <div class="feature" style="left:615px;top:190px">
    <svg width="52" height="52" viewBox="0 0 52 52"><path d="M26 46 6 26a11 11 0 0 1 20-14 11 11 0 0 1 20 14z" fill="none" stroke="#111" stroke-width="3"/><path d="M16 26h20M19 22v8M33 22v8" stroke="#111" stroke-width="3"/></svg>
    <h4>Workout Equipment Included<br>So You Can Train From Home</h4>
    <p>Your pack arrives with everything needed to start, so there is no gym, no travel and no childcare to arrange. Simply roll out your mat and train while your little one plays or sleeps nearby.</p>
    <div class="btn btn-solid">Read More</div>
  </div>

  <div class="feature" style="left:150px;top:488px">
    <svg width="52" height="52" viewBox="0 0 52 52"><g fill="none" stroke="#111" stroke-width="3"><rect x="14" y="16" width="24" height="32" rx="4"/><path d="M18 16V8h16v8M14 28h24"/></g></svg>
    <h4>Delicious Low Fat Family<br>Friendly Recipes</h4>
    <p>Quick meals the whole family will enjoy, with simple ingredients and easy steps. Each recipe is balanced to fuel your energy, support feeding and help you reach your goals without dieting.</p>
    <div class="btn btn-solid">Read More</div>
  </div>

  <div class="feature" style="left:615px;top:488px">
    <svg width="52" height="52" viewBox="0 0 52 52"><g fill="none" stroke="#111" stroke-width="3"><path d="M16 4h20l-4 16H20z"/><circle cx="26" cy="34" r="12"/><path d="m21 34 4 4 7-8"/></g></svg>
    <h4>Cater For Mums At All Stages Of<br>Post Baby Recovery</h4>
    <p>Whether your baby is six weeks or six years old, the stages adjust to where you are now. Start gently, build steadily and move forward only when your body feels ready for more.</p>
    <div class="btn btn-solid">Read More</div>
  </div>
</section>

<section class="cta" role="img" aria-label="Blue tinted photo of mums exercising together">
  <h2>Take the first step today by joining our program<br>and let us help you bounce back to the body that you deserve!</h2>
  <div class="btn btn-ghost" style="left:485px;top:259px;width:228px;height:54px;background:rgba(0,0,0,.25);border-color:transparent">Get Started</div>
</section>

<footer class="site-footer">
  <div class="footer-brand"><span class="brand-dot"></span>Harbourleaf Mums</div>
  <div class="f-col" style="left:273px;width:290px">
    <h5>About Us</h5>
    <p>Harbourleaf Mums helps new mums rebuild strength and confidence with safe home workouts, simple recipes and a caring community, so every mum can feel healthy, happy and strong again.</p>
  </div>
  <div class="f-col" style="left:620px">
    <h5>Quick Links</h5>
    <ul><li>Home</li><li>About Us</li><li>Program</li><li>Blog</li><li>Shop</li><li>Contact</li></ul>
  </div>
  <div class="f-col" style="left:766px">
    <h5>Other Links</h5>
    <ul><li>Terms of Service</li><li>Privacy Policy</li><li>FAQ</li><li>Disclaimer</li></ul>
  </div>
  <div class="f-col" style="left:924px">
    <h5>Connect With Us</h5>
    <svg width="40" height="14" viewBox="0 0 40 14"><circle cx="6" cy="7" r="5" fill="#999"/><circle cx="24" cy="7" r="5" fill="#999"/></svg>
  </div>
  <div class="copyright">© 2017 Harbourleaf Mums. All rights reserved.</div>
</footer>

<div class="scrim"></div>

<div class="popup">
  <div class="popup-photo" role="img" aria-label="Soft background photo of a smiling mum"></div>
  <div class="popup-close"><svg width="26" height="26" viewBox="0 0 26 26"><path d="M8 8l10 10M18 8 8 18" stroke="#333" stroke-width="2.5"/></svg></div>
  <h2>MY SIGHT OFFERING</h2>
  <h3>My Free Report</h3>
  <div class="email">Enter Your E-mail Address</div>
  <div class="btn btn-solid subscribe">Subscribe Now</div>
</div>

</body>
</html>
```